Economics of an Assumption vs Obtaining a New Loan at Current Market Rate

I need to marketing flyer that has fields that calculate mortgage payments amongst other calculations. I have a rough draft that I will attach.

The idea is to provide a tool for a real estate agent to use to illustrate to a potential buyer what a payment would be if they assumed the existing loan on the house or took out a new loan at current market.

The flyer needs to be able to allow an agent to drop in their logo, photo, and contact along with the loan officers photo and contact info.

You can google open house flyer to see examples of what the overall artwork and presentation can look like.

Target Market(s)

Home Buyers

Industry/Entity Type

Real Estate

Colors
F0912C
F2A743
F7CA91
FBE8D2
FDF5EE
EE7325
F08F49
F5BC92
FAE3D3
FDF4ED

Requirements
Must have
• A way to calculate mortgage payment
Nice to have
• Photo and logo drop ins

```html
<!DOCTYPE html>
<html lang="en">
<head>
<meta charset="utf-8">
<title>Orvane – Assumption vs New Loan Flyer</title>
<link href="https://fonts.googleapis.com/css2?family=Poppins:wght@400;500;600;700;800&family=Oswald:wght@500;600&display=swap" rel="stylesheet">
<style>
  :root{
    --orange:#EE7325;
    --orange-soft:#F0912C;
    --ink:#121212;
    --paper:#ffffff;
    --quote-grey:#c9c9c9;
    --bg:#e4e4e4;
  }
  *{box-sizing:border-box;margin:0;padding:0}
  html,body{width:865px;height:1200px;overflow:hidden;background:var(--bg)}
  body{font-family:'Poppins',sans-serif;color:var(--ink)}
  .flyer{position:relative;width:865px;height:1200px;background:var(--paper);overflow:hidden}
  .abs{position:absolute}

  /* hero */
  .hero-photo{left:0;top:0;width:865px;height:454px;
    background:linear-gradient(180deg,#8fc3ee 0%,#d6e8f6 28%,#eef4f8 42%,#b89575 58%,#a07c5e 72%,#8b6b52 82%,#a59e95 92%,#8f8780 100%)}
  .brand{left:62px;top:64px;display:flex;align-items:center;gap:12px}
  .brand-mark{width:34px;height:34px;background:var(--orange)}
  .brand-name{font-weight:500;font-size:54px;line-height:1;color:var(--ink);letter-spacing:-1px}
  .price-label{left:338px;top:62px;font-size:26px;line-height:24px}
  .price-label b{display:block;color:var(--orange);font-weight:700}
  .price-label span{font-weight:400}
  .price-box{left:507px;top:44px;width:296px;height:190px;background:var(--ink);border-radius:16px 16px 0 0;color:#fff;
    font-family:'Oswald',sans-serif;font-weight:500;font-size:54px;padding:14px 0 0 16px;letter-spacing:-0.5px}
  .price-box sup{font-size:24px;vertical-align:top;position:relative;top:6px}

  /* calculator */
  .black-band{left:0;top:648px;width:865px;height:138px;background:var(--ink)}
  .panel-head{top:448px;height:46px;background:var(--ink);border-radius:10px 10px 0 0;color:#fff;
    font-weight:700;font-size:19px;display:flex;align-items:center;justify-content:center;gap:10px;letter-spacing:.5px}
  .panel-head .pct{color:var(--orange);font-size:26px;font-weight:800}
  .panel-head small{font-size:9px;line-height:9px;font-weight:700}
  .panel{top:493px;height:190px;background:var(--orange);border-radius:0 0 12px 12px;color:#fff}
  .row{position:absolute;left:20px;right:20px;height:22px;display:flex;align-items:center;font-size:13px;font-weight:500}
  .row .label{flex:0 0 160px}
  .pill{background:#fff;color:var(--ink);border-radius:11px;height:22px;font-size:12.5px;display:flex;align-items:center;padding-left:24px;flex:1;white-space:nowrap;overflow:hidden}
  .pill.center{justify-content:center;padding-left:0}
  .row .total{font-weight:700;font-size:17px;flex:0 0 auto;margin-right:12px}
  .row .mini{font-size:12px;flex:0 0 auto;margin:0 10px}
  .delta{top:708px;left:56px;right:62px;display:flex;align-items:center;color:#fff;font-size:14px}
  .delta .tag{color:var(--orange);font-weight:700;margin-right:10px}
  .delta .outline{border:1.5px solid var(--orange);border-radius:12px;padding:1px 10px;font-size:13.5px}
  .delta .dp{margin-left:30px;font-size:14px}
  .delta .dp-field{margin-left:12px;background:#fff;border-radius:11px;height:22px;width:140px}
  .diff{top:742px;left:56px;right:62px;display:flex;align-items:center;color:#fff;font-weight:700;font-size:24px;letter-spacing:.3px}
  .diff .rule{width:2px;height:28px;background:var(--orange);margin:0 16px}

  /* certification */
  .seal{left:56px;top:810px}
  .quote-open{left:230px;top:834px}
  .quote-close{left:594px;top:904px}
  .cert-lead{left:328px;top:836px;font-size:20px;line-height:24px;letter-spacing:5px;font-weight:500}
  .cert-title{left:326px;top:860px;color:var(--orange);font-weight:800;font-size:44px;line-height:45px;letter-spacing:.5px}

  /* contacts */
  .agent-photo{left:55px;top:979px;width:181px;height:221px;border-radius:12px 12px 0 0;
    background:linear-gradient(160deg,#2b3442 0%,#6d7280 35%,#c9c2b6 60%,#b8935a 80%,#8fa28a 100%)}
  .card{top:979px;width:180px;height:221px;background:var(--orange);border-radius:12px 12px 0 0;color:var(--ink);text-align:center}
  .card-tab{position:absolute;top:0;left:6px;right:6px;height:22px;background:var(--ink);color:#fff;font-size:11px;font-weight:700;
    border-radius:0 0 8px 8px;display:flex;align-items:center;justify-content:center}
  .card ul{list-style:none;padding-top:72px;font-size:15.5px;font-weight:500}
  .card li{margin-bottom:12px}
  .card svg{display:block;margin:0 auto 2px}
  .logo-card{left:621px;top:979px;width:182px;height:221px;background:var(--ink);border-radius:12px 12px 0 0;
    display:flex;align-items:center;justify-content:center;gap:8px}
  .logo-card .brand-mark{width:16px;height:16px}
  .logo-card .brand-name{color:var(--orange);font-size:30px;letter-spacing:0}
</style>
</head>
<body>
<main class="flyer">
  <div class="abs hero-photo" role="img" aria-label="Property photo: stucco single-storey home with tiled roof under a blue sky"></div>

  <div class="abs brand"><span class="brand-mark"></span><span class="brand-name">Orvane</span></div>
  <div class="abs price-label"><b>PURCHASE</b><span>PRICE</span></div>
  <div class="abs price-box"><sup>$</sup>1,720,0000</div>

  <div class="abs black-band"></div>

  <!-- current mortgage -->
  <div class="abs panel-head" style="left:46px;width:374px">CURRENT MORTGAGE</div>
  <div class="abs panel" style="left:55px;width:364px">
    <div class="row" style="top:13px"><span class="label">Loan amount</span><span class="pill">Allow Input</span></div>
    <div class="row" style="top:43px"><span class="label">Interest rate</span><span class="pill">Allow Input</span></div>
    <div class="row" style="top:72px"><span class="label">Principle Interest</span><span class="pill">Allow Input</span></div>
    <div class="row" style="top:102px"><span class="label">Mortgage Insurance</span><span class="pill">Allow Input</span></div>
    <div class="row" style="top:132px"><span class="total">TOTAL</span><span class="pill"></span></div>
    <div class="row" style="top:160px"><span class="mini" style="margin-left:4px">Years</span><span class="pill" style="flex:0 0 66px"></span><span class="mini">Months</span><span class="pill" style="flex:0 0 66px"></span><span class="mini" style="margin-right:0">left on loan</span></div>
  </div>

  <!-- new mortgage -->
  <div class="abs panel-head" style="left:433px;width:374px">NEW MORTGAGE <span class="pct">10%</span><small>DOWN<br>PAYMENT</small></div>
  <div class="abs panel" style="left:443px;width:364px">
    <div class="row" style="top:13px"><span class="label">Loan amount</span><span class="pill" style="padding-left:18px">70% of purchase price</span></div>
    <div class="row" style="top:43px"><span class="label">Market Rate</span><span class="pill">Input</span></div>
    <div class="row" style="top:72px"><span class="label">Principle Interest</span><span class="pill">Calc payment</span></div>
    <div class="row" style="top:102px"><span class="label">Mortgage Insurance</span><span class="pill">Input %</span></div>
    <div class="row" style="top:132px"><span class="total">TOTAL</span><span class="pill center" style="font-size:11.5px">Principal Interest + Mortgage Insurance</span></div>
    <div class="row" style="top:160px"><span class="mini" style="margin-left:0;flex:0 0 50px">Term</span><span class="pill"></span><span class="mini" style="margin-right:0">Years</span></div>
  </div>

  <div class="abs delta"><span class="tag">DELTA</span><span class="outline">PURCHASE PRICE MINUS LOAN AMOUNT</span><span class="dp">DOWN PAYMENT AMOUNT</span><span class="dp-field"></span></div>
  <div class="abs diff"><span>PAYMENT DIFFERENCE</span><span class="rule"></span><span>DIFFERENCE BETWEEN TOTALS</span></div>

  <!-- certification -->
  <svg class="abs seal" width="140" height="140" viewBox="0 0 140 140" role="img" aria-label="Certification seal">
    <circle cx="70" cy="70" r="66" fill="var(--ink)"/>
    <circle cx="70" cy="70" r="58" fill="#fff"/>
    <circle cx="70" cy="70" r="36" fill="var(--orange)"/>
    <path d="M53 70 L66 84 L90 56" fill="none" stroke="#fff" stroke-width="9" stroke-linecap="round" stroke-linejoin="round"/>
  </svg>

  <svg class="abs quote-open" width="84" height="62" viewBox="0 0 84 62" aria-hidden="true">
    <g fill="var(--quote-grey)">
      <circle cx="20" cy="42" r="18"/><path d="M3 40 Q4 8 34 2 L36 12 Q18 18 16 32 Z"/>
      <circle cx="62" cy="42" r="18"/><path d="M45 40 Q46 8 76 2 L78 12 Q60 18 58 32 Z"/>
    </g>
  </svg>
  <div class="abs cert-lead">THIS PROPERTY IS</div>
  <div class="abs cert-title">LOW RATE ASSUMED<br>CERTIFIED</div>
  <svg class="abs quote-close" width="84" height="62" viewBox="0 0 84 62" aria-hidden="true">
    <g fill="var(--quote-grey)" transform="rotate(180 42 31)">
      <circle cx="20" cy="42" r="18"/><path d="M3 40 Q4 8 34 2 L36 12 Q18 18 16 32 Z"/>
      <circle cx="62" cy="42" r="18"/><path d="M45 40 Q46 8 76 2 L78 12 Q60 18 58 32 Z"/>
    </g>
  </svg>

  <!-- contacts -->
  <div class="abs agent-photo" role="img" aria-label="Photo drop-in: house model with stacked coins and cash"></div>

  <section class="abs card" style="left:244px">
    <div class="card-tab">CONTACT INFORMATION</div>
    <ul>
      <li><svg width="12" height="12" viewBox="0 0 24 24"><path d="M6 2l4 4-2 3c1 3 4 6 7 7l3-2 4 4-3 4C11 22 2 13 2 5z" fill="#fff"/></svg>555 010 2468</li>
      <li><svg width="14" height="11" viewBox="0 0 24 18"><rect x="1" y="1" width="22" height="16" fill="#fff"/><path d="M1 1l11 9 11-9" fill="none" stroke="var(--orange)" stroke-width="2"/></svg>hello@orvane.com</li>
      <li><svg width="13" height="13" viewBox="0 0 24 24"><circle cx="12" cy="12" r="10" fill="#fff"/><path d="M2 12h20M12 2c4 4 4 16 0 20M12 2c-4 4-4 16 0 20" fill="none" stroke="var(--orange)" stroke-width="1.6"/></svg>www.orvane.com</li>
    </ul>
  </section>

  <section class="abs card" style="left:433px">
    <div class="card-tab">CONTACT INFORMATION</div>
    <ul>
      <li><svg width="12" height="12" viewBox="0 0 24 24"><path d="M6 2l4 4-2 3c1 3 4 6 7 7l3-2 4 4-3 4C11 22 2 13 2 5z" fill="#fff"/></svg>555 010 2468</li>
      <li><svg width="14" height="11" viewBox="0 0 24 18"><rect x="1" y="1" width="22" height="16" fill="#fff"/><path d="M1 1l11 9 11-9" fill="none" stroke="var(--orange)" stroke-width="2"/></svg>hello@orvane.com</li>
      <li><svg width="13" height="13" viewBox="0 0 24 24"><circle cx="12" cy="12" r="10" fill="#fff"/><path d="M2 12h20M12 2c4 4 4 16 0 20M12 2c-4 4-4 16 0 20" fill="none" stroke="var(--orange)" stroke-width="1.6"/></svg>www.orvane.com</li>
    </ul>
  </section>

  <div class="abs logo-card"><span class="brand-mark"></span><span class="brand-name">Orvane</span></div>
</main>
</body>
</html>
```